Business Card Design Project

Basic business card with minimal details. I just need company name, email & web address, telephone and my name.
I would like the back of the card to be grey with my logo & company name centred.

Target Market(s)

Architects
Builders
Property Developers

Industry/Entity Type

Business

Font styles to use
Sans Serif

Colors

Designer to choose colors to be used in the design.

Requirements
Must have
• Tallow Crest
Rupert Hazelby - Director
M: 0427 915203
E: rupert@tallowcrest.com.au
W: www.tallowcrest.com.au
Should not have
• No other images or pictures

```html
<!DOCTYPE html>
<html lang="en">
<head>
<meta charset="utf-8">
<title>Tallow Crest – Business Card</title>
<link href="https://fonts.googleapis.com/css2?family=Arimo:wght@400;700&display=swap" rel="stylesheet">
<style>
  :root {
    --stage: #ececec;
    --card-grey: #c2c2c2;
    --card-white: #ffffff;
    --brand-slate: #3f4a55;
    --brand-red: #8e1b33;
    --name-grey: #8c8c8c;
    --role-grey: #9a9a9a;
    --icon-grey: #888888;
    --contact-text: #ffffff;
  }
  html, body {
    margin: 0;
    padding: 0;
    width: 1200px;
    height: 999px;
    overflow: hidden;
    background: var(--stage);
    font-family: "Arimo", Arial, sans-serif;
  }
  .canvas {
    position: relative;
    width: 1200px;
    height: 999px;
  }
  .card {
    position: absolute;
    left: 286px;
    width: 631px;
    box-shadow: 0 1px 4px rgba(0,0,0,0.08);
  }
  .card-front {
    top: 128px;
    height: 360px;
    background: var(--card-grey);
  }
  .brand {
    position: absolute;
    left: 0;
    right: 0;
    top: 0;
    bottom: 0;
    display: flex;
    align-items: center;
    justify-content: center;
    gap: 22px;
    margin-top: -4px;
  }
  .brand-square {
    width: 44px;
    height: 44px;
    background: var(--brand-red);
  }
  .brand-name {
    font-size: 50px;
    font-weight: 400;
    letter-spacing: 2px;
    text-transform: uppercase;
    color: var(--brand-slate);
    line-height: 1;
  }
  .card-back {
    top: 507px;
    height: 362px;
    background: var(--card-grey);
  }
  .identity-band {
    position: absolute;
    left: 0;
    top: 0;
    width: 100%;
    height: 128px;
    background: var(--card-white);
  }
  .person-name {
    position: absolute;
    left: 27px;
    top: 17px;
    margin: 0;
    font-size: 27px;
    font-weight: 700;
    letter-spacing: 0.3px;
    text-transform: uppercase;
    color: var(--name-grey);
  }
  .person-role {
    position: absolute;
    left: 27px;
    top: 50px;
    margin: 0;
    font-size: 20px;
    color: var(--role-grey);
  }
  .contact-list {
    position: absolute;
    left: 26px;
    top: 156px;
    margin: 0;
    padding: 0;
    list-style: none;
  }
  .contact-item {
    display: flex;
    align-items: center;
    height: 30px;
    margin-bottom: 33px;
    font-size: 20px;
    color: var(--contact-text);
  }
  .contact-icon {
    width: 36px;
    height: 30px;
    margin-right: 10px;
    flex: none;
  }
</style>
</head>
<body>
<main class="canvas">
  <section class="card card-front" aria-label="Card front">
    <div class="brand">
      <span class="brand-square" aria-hidden="true"></span>
      <span class="brand-name">Tallow Crest</span>
    </div>
  </section>

  <section class="card card-back" aria-label="Card back">
    <div class="identity-band">
      <h1 class="person-name">Rupert Hazelby</h1>
      <p class="person-role">Director</p>
    </div>
    <ul class="contact-list">
      <li class="contact-item">
        <svg class="contact-icon" viewBox="0 0 36 30" aria-hidden="true">
          <rect x="2" y="1" width="14" height="27" rx="2" fill="none" stroke="var(--icon-grey)" stroke-width="1.3"/>
          <line x1="2" y1="22" x2="16" y2="22" stroke="var(--icon-grey)" stroke-width="1.1"/>
          <circle cx="9" cy="25" r="1.2" fill="var(--icon-grey)"/>
        </svg>
        <span>0427 915203</span>
      </li>
      <li class="contact-item">
        <svg class="contact-icon" viewBox="0 0 36 30" aria-hidden="true">
          <rect x="1" y="9" width="26" height="14" fill="none" stroke="var(--icon-grey)" stroke-width="1.3"/>
          <polyline points="1,9 14,18 27,9" fill="none" stroke="var(--icon-grey)" stroke-width="1.2"/>
          <line x1="1" y1="23" x2="11" y2="15" stroke="var(--icon-grey)" stroke-width="1"/>
          <line x1="27" y1="23" x2="17" y2="15" stroke="var(--icon-grey)" stroke-width="1"/>
        </svg>
        <span>rupert@tallowcrest.com.au</span>
      </li>
      <li class="contact-item">
        <svg class="contact-icon" viewBox="0 0 36 30" aria-hidden="true">
          <text x="0" y="14" font-family="Arimo, Arial, sans-serif" font-size="10" fill="var(--icon-grey)">www</text>
          <path d="M22 10 L22 26 L25.5 22.5 L28.5 29 L30.5 28 L27.5 21.8 L32 21.5 Z" fill="var(--card-white)" stroke="var(--icon-grey)" stroke-width="1"/>
        </svg>
        <span>www.tallowcrest.com.au</span>
      </li>
    </ul>
  </section>
</main>
</body>
</html>
```